Need Web Design for Business Process Outsourcing Company (Quorvane)

Quorvane is a business process outsourcing company. Need a simple site similar to http://www.tallowbrinkhire.com/ but with a more professional and credible look. New to the process; not sure where to start and comparing my options. Please let me know what my options are if I choose to go with you. Logo is attached for your reference. Please use same colorway

Reason: I want the final product to be coded. Please confirm you will be able to code final design.

Industry/Entity Type

Business

Coding

Coded - Design and coding required

```html
<!DOCTYPE html>
<html lang="en">
<head>
<meta charset="utf-8">
<title>Quorvane — Outsourcing Business Services</title>
<link href="https://fonts.googleapis.com/css2?family=Oswald:wght@400;500;600&family=Open+Sans:wght@400;600;700&family=Roboto+Slab:wght@400;600&display=swap" rel="stylesheet">
<style>
:root{
  --blue:#1b8fd2;
  --blue-dark:#1474ad;
  --ink:#222b33;
  --text:#5d6670;
  --black:#111214;
  --navy:#0f2233;
  --navy-deep:#0a1724;
  --white:#ffffff;
  --line:#d9dee3;
}
*{box-sizing:border-box;margin:0;padding:0}
html,body{width:1200px;height:4736px;overflow:hidden}
body{font-family:"Open Sans",Arial,sans-serif;color:var(--text);background:var(--white);position:relative}
section,header,nav,footer{position:absolute;left:0;width:1200px}
.btn{display:inline-block;font-family:"Open Sans",Arial,sans-serif;font-weight:600;text-decoration:none;text-align:center;letter-spacing:.5px}
.section-title{font-family:"Open Sans",Arial,sans-serif;font-weight:400;font-size:36px;color:var(--ink);text-align:center;display:flex;align-items:center;justify-content:center;gap:14px}
.section-title b{font-weight:400;color:var(--blue)}
.title-mark{width:30px;height:30px;background:var(--blue);display:inline-block}

/* header */
.site-header{top:0;height:128px;background:var(--white)}
.brand{position:absolute;left:40px;top:30px;display:flex;align-items:center;gap:14px}
.brand-square{width:62px;height:62px;background:var(--blue)}
.brand-name{font-family:"Open Sans",Arial,sans-serif;font-weight:700;font-size:52px;color:var(--blue);letter-spacing:-1px}
.header-links{position:absolute;right:40px;top:18px;display:flex;gap:30px;font-size:18px;color:var(--ink);align-items:center}
.header-links span{display:flex;align-items:center;gap:10px}
.header-phone{position:absolute;right:40px;top:66px;font-size:19px;color:var(--ink);font-weight:600}

.main-nav{top:128px;height:64px;background:var(--black);display:flex;padding-left:70px}
.main-nav a{color:var(--white);text-decoration:none;font-size:18px;padding:0 22px;line-height:64px}
.main-nav a.active{background:var(--blue)}

/* hero */
.hero{top:192px;height:576px;overflow:hidden}
.hero-photo{position:absolute;inset:0;background:linear-gradient(100deg,#3b4550 0%,#5b6975 35%,#8b9aa6 55%,#4d5a66 75%,#2b3540 100%)}
.hero-copy{position:absolute;left:76px;top:150px;color:var(--white)}
.hero-copy h1{font-family:"Oswald",Arial,sans-serif;font-weight:500;font-size:98px;line-height:1;letter-spacing:1px}
.hero-copy p{font-family:"Oswald",Arial,sans-serif;font-size:44px;margin-top:12px}
.hero-copy .btn{margin-top:36px;background:var(--blue);color:var(--white);font-size:20px;padding:16px 34px}

/* welcome */
.welcome{top:768px;height:304px;text-align:center}
.welcome .section-title{margin-top:52px}
.welcome p{width:800px;margin:28px auto 0;font-size:15px;line-height:26px;color:var(--text)}
.welcome .btn{margin-top:34px;background:var(--black);color:var(--white);font-size:15px;padding:14px 26px}

/* about */
.about{top:1072px;height:748px;overflow:hidden}
.about-bg{position:absolute;inset:0;background:linear-gradient(180deg,#eaf2f7 0%,#c9dbe6 45%,#a5bfd0 100%)}
.about .section-title{position:relative;margin-top:36px}
.who-panel{position:absolute;left:80px;top:92px;width:500px;height:608px;background:rgba(27,143,210,.88);padding:30px 26px;color:var(--white)}
.who-panel h3{font-family:"Roboto Slab",Georgia,serif;font-weight:600;font-size:38px;color:var(--navy-deep);margin-bottom:24px}
.who-panel p{font-size:17px;line-height:37px;color:#0e2538}
.about-list{position:absolute;left:636px;top:92px;width:484px}
.about-item{display:flex;gap:18px;height:120px;padding-top:6px}
.about-thumb{width:104px;height:96px;flex:none;background:linear-gradient(135deg,#587285,#a9bccb)}
.about-item h4{font-size:19px;font-weight:600;color:var(--blue)}
.about-item p{font-size:13px;line-height:19px;color:var(--ink);margin-top:4px}
.read-link{font-size:13px;font-weight:700;color:var(--blue-dark);margin-top:4px;display:block}

/* services */
.services{top:1820px;height:440px;text-align:center}
.services .section-title{margin-top:40px}
.service-row{display:flex;justify-content:center;gap:46px;margin-top:44px}
.service{width:180px}
.service-icon{width:120px;height:120px;border-radius:50%;background:var(--blue);margin:0 auto;display:flex;align-items:center;justify-content:center}
.service h4{font-size:18px;font-weight:400;color:var(--blue);margin-top:22px}
.service p{font-size:14px;line-height:20px;color:var(--text);margin-top:6px}
.services .more{display:inline-block;margin-top:30px;font-size:20px;color:var(--ink);border-bottom:2px solid var(--ink);padding-bottom:4px}

/* strategy */
.strategy{top:2260px;height:800px;overflow:hidden}
.strategy-bg{position:absolute;inset:0;background:linear-gradient(180deg,#2a3f54 0%,#1b2c3d 50%,#223547 100%)}
.strategy h2{position:relative;text-align:center;font-family:"Open Sans",Arial,sans-serif;font-weight:400;font-size:34px;color:var(--blue);margin-top:26px;letter-spacing:1px}
.strategy svg.map{position:absolute;left:0;top:0}
.strategy-item{position:absolute;width:220px;font-size:17px;line-height:24px;color:var(--white)}
.strategy-item.left{text-align:right}
.strategy .btn{position:absolute;left:508px;top:720px;width:184px;border:3px solid var(--white);color:var(--white);font-size:20px;padding:10px 0;background:rgba(0,0,0,.25)}

/* experience / security */
.exp-sec{top:3060px;height:560px}
.exp-col{position:absolute;top:36px;width:420px;text-align:center}
.exp-col h2{font-family:"Open Sans",Arial,sans-serif;font-weight:400;font-size:34px;color:var(--ink)}
.exp-col h2 b{font-weight:400;color:var(--blue)}
.exp-img{width:420px;height:250px;margin-top:18px}
.exp-col h4{font-size:18px;font-weight:400;color:var(--blue);margin-top:14px}
.exp-col p{font-size:14px;line-height:21px;color:var(--text);margin-top:6px}
.exp-sec .btn{position:absolute;left:504px;top:484px;width:192px;border:4px solid var(--blue);color:var(--ink);font-size:19px;padding:10px 0}

/* blogs */
.blogs{top:3620px;height:420px;overflow:hidden}
.blogs-bg{position:absolute;inset:0;background:linear-gradient(180deg,#2d6f9e 0%,#9dc2da 55%,#e4edf3 100%)}
.blogs h2{position:relative;text-align:center;font-family:"Open Sans",Arial,sans-serif;font-weight:400;font-size:38px;color:var(--navy);margin-top:22px;letter-spacing:1px}
.blogs h2 b{font-weight:400;color:var(--blue)}
.blog-row{position:absolute;left:72px;top:92px;display:flex;gap:28px}
.blog-card{width:336px}
.blog-img{height:156px}
.blog-card h4{font-size:15px;font-weight:600;color:var(--navy);margin-top:12px}
.blog-date{font-size:12px;color:var(--blue-dark);margin-top:4px;display:flex;align-items:center;gap:6px}
.blog-card p{font-size:13px;line-height:19px;color:var(--ink);margin-top:6px}

/* band */
.join-band{top:4040px;height:100px;background:var(--blue)}
.join-band p{position:absolute;left:80px;top:24px;width:900px;font-size:14px;line-height:24px;color:var(--white)}
.join-band .btn{position:absolute;right:80px;top:30px;background:var(--white);color:var(--ink);font-size:15px;padding:10px 26px;border-radius:22px}

/* contact */
.contact{top:4140px;height:500px;background:var(--navy)}
.contact h3{position:absolute;top:36px;font-family:"Open Sans",Arial,sans-serif;font-weight:400;font-size:28px;color:var(--white);letter-spacing:.5px}
.field{position:absolute;border:1px solid #9fb0c0;background:transparent;font-size:13px;color:#c7d2dc;padding:8px 10px}
.contact .submit{position:absolute;left:80px;top:304px;width:116px;background:var(--blue);color:var(--white);font-size:14px;padding:9px 0}
.info-item{position:absolute;left:600px;display:flex;align-items:center;gap:16px;font-size:15px;color:#d5dee6}
.social{position:absolute;top:410px;left:600px;display:flex;gap:26px}
.social span{width:40px;height:40px;border-radius:50%;background:var(--blue)}

.site-footer{top:4640px;height:96px;background:var(--navy-deep);text-align:center;line-height:96px;font-size:15px;color:var(--white);border-top:1px solid #24384b}
.site-footer b{font-weight:700}
</style>
</head>
<body>

<header class="site-header">
  <div class="brand"><span class="brand-square"></span><span class="brand-name">Quorvane</span></div>
  <div class="header-links">
    <span><svg width="30" height="22" viewBox="0 0 30 22"><path d="M2 2h18v12H9l-5 4v-4H2z" fill="#1b8fd2"/><path d="M22 6h6v10h-2v4l-4-4h-8v-2h8z" fill="#1b8fd2"/></svg>Live Chat</span>
    <span><svg width="26" height="20" viewBox="0 0 26 20"><rect x="1" y="2" width="24" height="16" fill="#1b8fd2"/><path d="M1 2l12 9 12-9" fill="none" stroke="#fff" stroke-width="2"/></svg>Email Us</span>
  </div>
  <div class="header-phone"><svg width="18" height="18" viewBox="0 0 24 24" style="vertical-align:-3px;margin-right:8px"><path d="M6 2l4 5-2 3c1 3 3 5 6 6l3-2 5 4-2 4C10 22 2 14 2 4z" fill="#1b8fd2"/></svg>1-888-555-0142</div>
</header>

<nav class="main-nav">
  <a class="active">HOME</a><a>ABOUT US</a><a>SERVICES</a><a>STRATEGY</a><a>EXPERIENCE</a><a>SECURITY</a><a>NEWS</a><a>CONTACT US</a>
</nav>

<section class="hero">
  <div class="hero-photo" role="img" aria-label="Office building backdrop with a smiling consultant holding a laptop"></div>
  <div class="hero-copy">
    <h1>OUT SOURCING</h1>
    <p>BEST FOR YOUR BUSINESS</p>
    <a class="btn">JOIN US NOW</a>
  </div>
</section>

<section class="welcome">
  <h2 class="section-title"><span class="title-mark"></span>Welcome To <b>Outsourcing Business Services</b></h2>
  <p>Lorem Ipsum is simply dummy text of the printing and typesetting industry. Lorem Ipsum has been the industry's standard dummy text ever since the 1500s, when an unknown printer took a galley of type and scrambled it to make a type specimen book.</p>
  <a class="btn">READ MORE</a>
</section>

<section class="about">
  <div class="about-bg" role="img" aria-label="Desk with laptop and business paperwork"></div>
  <h2 class="section-title"><span class="title-mark"></span>About <b>Outsourcing Business</b></h2>
  <div class="who-panel">
    <h3>Who We Are...</h3>
    <p>Quorvane is a managed outsourcing service. We help businesses from around the world reduce overhead, complete projects and extend their companies overall output by providing a scalable workforce. We have a service that can help your business right now. Whether you are large corporation or a small business we have a solution that will fit with your business plan.</p>
  </div>
  <div class="about-list">
    <div class="about-item"><div class="about-thumb" role="img" aria-label="Company office photo"></div><div><h4>Our Company</h4><p>Quorvane gives access to a large pool of employees with a wide range of skill sets.</p><span class="read-link">READ MORE</span></div></div>
    <div class="about-item"><div class="about-thumb" role="img" aria-label="Team culture photo"></div><div><h4>Our Culture</h4><p>Quorvane gives access to a large pool of employees with a wide range of skill sets.</p><span class="read-link">READ MORE</span></div></div>
    <div class="about-item"><div class="about-thumb" role="img" aria-label="Staff members photo"></div><div><h4>Our People</h4><p>Quorvane gives access to a large pool of employees with a wide range of skill sets.</p><span class="read-link">READ MORE</span></div></div>
    <div class="about-item"><div class="about-thumb" role="img" aria-label="Company history photo"></div><div><h4>Our Story</h4><p>Quorvane gives access to a large pool of employees with a wide range of skill sets.</p><span class="read-link">READ MORE</span></div></div>
    <div class="about-item"><div class="about-thumb" role="img" aria-label="Office facilities photo"></div><div><h4>Our Facilities</h4><p>Quorvane gives access to a large pool of employees with a wide range of skill sets.</p><span class="read-link">READ MORE</span></div></div>
  </div>
</section>

<section class="services">
  <h2 class="section-title"><span class="title-mark"></span>Our Best <b>Services</b></h2>
  <div class="service-row">
    <div class="service"><div class="service-icon"><svg width="56" height="56" viewBox="0 0 56 56" fill="none" stroke="#fff" stroke-width="4"><path d="M10 32V26a18 18 0 0 1 36 0v6"/><rect x="6" y="30" width="10" height="16" rx="3" fill="#fff"/><rect x="40" y="30" width="10" height="16" rx="3" fill="#fff"/></svg></div><h4>Customer Service</h4><p>Lorem ipsum simply dummy of the printing</p></div>
    <div class="service"><div class="service-icon"><svg width="56" height="56" viewBox="0 0 56 56" fill="none" stroke="#fff" stroke-width="4"><path d="M4 10h8l6 24h26l6-18H15"/><circle cx="22" cy="44" r="4" fill="#fff"/><circle cx="40" cy="44" r="4" fill="#fff"/></svg></div><h4>Ecommerce</h4><p>Lorem ipsum simply dummy of the printing</p></div>
    <div class="service"><div class="service-icon"><svg width="56" height="56" viewBox="0 0 56 56" fill="none" stroke="#fff" stroke-width="4"><circle cx="28" cy="28" r="20"/><circle cx="20" cy="22" r="4" fill="#fff"/><circle cx="34" cy="18" r="4" fill="#fff"/><circle cx="38" cy="32" r="4" fill="#fff"/></svg></div><h4>Creative</h4><p>Lorem ipsum simply dummy of the printing</p></div>
    <div class="service"><div class="service-icon"><svg width="56" height="56" viewBox="0 0 56 56" fill="none" stroke="#fff" stroke-width="4"><rect x="6" y="10" width="44" height="28" rx="2"/><path d="M20 48h16M28 38v10"/></svg></div><h4>IT Solutions</h4><p>Lorem ipsum simply dummy of the printing</p></div>
    <div class="service"><div class="service-icon"><svg width="56" height="56" viewBox="0 0 56 56" fill="#fff"><circle cx="28" cy="18" r="8"/><path d="M14 46a14 14 0 0 1 28 0z"/><circle cx="12" cy="24" r="5"/><circle cx="44" cy="24" r="5"/></svg></div><h4>Human Resources</h4><p>Lorem ipsum simply dummy of the printing</p></div>
  </div>
  <span class="more">READ MORE</span>
</section>

<section class="strategy">
  <div class="strategy-bg" role="img" aria-label="Team meeting in a bright office"></div>
  <h2>OUR BEST STRATEGY</h2>
  <svg class="map" width="1200" height="800" viewBox="0 0 1200 800">
    <g stroke="#ffffff" stroke-opacity=".6" stroke-width="2" fill="none">
      <path d="M366 140 L520 300"/><path d="M366 268 L520 330"/><path d="M366 400 L520 380"/><path d="M366 528 L520 410"/>
      <path d="M834 140 L680 300"/><path d="M834 268 L680 330"/><path d="M834 400 L680 380"/><path d="M834 528 L680 410"/>
    </g>
    <circle cx="600" cy="355" r="86" fill="#ffffff"/>
    <circle cx="600" cy="355" r="70" fill="#1b8fd2"/>
    <g fill="#ffffff">
      <circle cx="330" cy="140" r="34"/><circle cx="330" cy="268" r="34"/><circle cx="330" cy="400" r="34"/><circle cx="330" cy="528" r="34"/>
      <circle cx="870" cy="140" r="34"/><circle cx="870" cy="268" r="34"/><circle cx="870" cy="400" r="34"/><circle cx="870" cy="528" r="34"/>
    </g>
    <g fill="#1b8fd2">
      <circle cx="320" cy="132" r="6"/><circle cx="340" cy="132" r="6"/><rect x="312" y="142" width="36" height="10" rx="4"/>
      <rect x="316" y="258" width="28" height="20" rx="3"/><circle cx="330" cy="268" r="5" fill="#fff"/>
      <ellipse cx="330" cy="398" rx="18" ry="12"/><path d="M320 406l-6 10 12-6z"/>
      <path d="M330 510l16 8v10c0 9-7 14-16 18-9-4-16-9-16-18v-10z"/>
      <path d="M856 150l14-20 14 20z"/>
      <rect x="856" y="258" width="28" height="20" rx="3"/>
      <circle cx="866" cy="398" r="10"/><rect x="873" y="405" width="12" height="5" transform="rotate(45 873 405)"/>
      <path d="M856 528l9 9 19-19" fill="none" stroke="#1b8fd2" stroke-width="5"/>
    </g>
  </svg>
  <div class="strategy-item left" style="left:70px;top:128px">Structured Hiring Process</div>
  <div class="strategy-item left" style="left:70px;top:256px">Optimizing Work Capacity</div>
  <div class="strategy-item left" style="left:70px;top:376px">Centralized Customer Communication and Escalation</div>
  <div class="strategy-item left" style="left:70px;top:516px">Thorough Employee Vetting</div>
  <div class="strategy-item" style="left:924px;top:128px">Business Critical and Zero Tolerance</div>
  <div class="strategy-item" style="left:924px;top:256px">Skill Set Resiliency and Contingency</div>
  <div class="strategy-item" style="left:924px;top:388px">Quality Analysis and Review</div>
  <div class="strategy-item" style="left:924px;top:516px">Operational Standardization</div>
  <a class="btn">VIEW ALL</a>
</section>

<section class="exp-sec">
  <div class="exp-col" style="left:150px">
    <h2>Our <b>Experience</b></h2>
    <div class="exp-img" role="img" aria-label="Business team gathered around a desk" style="background:linear-gradient(135deg,#c7d2dc,#6d8598)"></div>
    <h4>Lorem Ipsum is simply dummy text of the printing</h4>
    <p>Lorem Ipsum is simply dummy text of the printing and typesetting industry.</p>
  </div>
  <div class="exp-col" style="left:630px">
    <h2><b>Security</b></h2>
    <div class="exp-img" role="img" aria-label="Hands on a laptop with digital security graphics" style="background:linear-gradient(135deg,#1d4b73,#4f9bd0)"></div>
    <h4>Lorem Ipsum is simply dummy text of the printing</h4>
    <p>Lorem Ipsum is simply dummy text of the printing and typesetting industry.</p>
  </div>
  <a class="btn">READ MORE</a>
</section>

<section class="blogs">
  <div class="blogs-bg" role="img" aria-label="Blurred city skyline backdrop"></div>
  <h2>LATEST <b>BLOGS</b></h2>
  <div class="blog-row">
    <div class="blog-card"><div class="blog-img" role="img" aria-label="Consultant working at a laptop" style="background:linear-gradient(135deg,#dfe6ec,#8fa3b4)"></div><h4>Lorem Ipsum is simply text Dummy</h4><span class="blog-date"><svg width="12" height="12" viewBox="0 0 12 12"><rect x="1" y="2" width="10" height="9" fill="none" stroke="#1474ad"/></svg>16 April 2016</span><p>Lorem Ipsum is simply dummy text of the printing and typesetting industry.</p><span class="read-link">READ MORE ⇒</span></div>
    <div class="blog-card"><div class="blog-img" role="img" aria-label="Team meeting at a boardroom table" style="background:linear-gradient(135deg,#e7ecef,#9aa9b6)"></div><h4>Lorem Ipsum is simply text Dummy</h4><span class="blog-date"><svg width="12" height="12" viewBox="0 0 12 12"><rect x="1" y="2" width="10" height="9" fill="none" stroke="#1474ad"/></svg>16 April 2016</span><p>Lorem Ipsum is simply dummy text of the printing and typesetting industry.</p><span class="read-link">READ MORE ⇒</span></div>
    <div class="blog-card"><div class="blog-img" role="img" aria-label="Call centre agents with headsets" style="background:linear-gradient(135deg,#e3e8ec,#8c9aa7)"></div><h4>Lorem Ipsum is simply text Dummy</h4><span class="blog-date"><svg width="12" height="12" viewBox="0 0 12 12"><rect x="1" y="2" width="10" height="9" fill="none" stroke="#1474ad"/></svg>16 April 2016</span><p>Lorem Ipsum is simply dummy text of the printing and typesetting industry.</p><span class="read-link">READ MORE ⇒</span></div>
  </div>
</section>

<section class="join-band">
  <p>Lorem Ipsum is simply dummy text of the printing and typesetting industry. Lorem Ipsum has been the industry's standard dummy text ever since the 1500s, when an unknown printer took a galley of type and scrambled.</p>
  <a class="btn">JOIN US</a>
</section>

<section class="contact">
  <h3 style="left:80px">GET IN TOUCH WITH US</h3>
  <div class="field" style="left:80px;top:100px;width:188px;height:34px">Enter Name</div>
  <div class="field" style="left:282px;top:100px;width:188px;height:34px">Enter Contact No.</div>
  <div class="field" style="left:80px;top:146px;width:188px;height:34px">Enter E-Mail</div>
  <div class="field" style="left:80px;top:192px;width:390px;height:96px">Enter Message</div>
  <a class="btn submit">SUBMIT</a>

  <h3 style="left:600px">CONTACT INFO</h3>
  <div class="info-item" style="top:104px"><svg width="18" height="22" viewBox="0 0 18 22"><path d="M9 1a7 7 0 0 1 7 7c0 5-7 13-7 13S2 13 2 8a7 7 0 0 1 7-7z" fill="#fff"/><circle cx="9" cy="8" r="3" fill="#0f2233"/></svg>Lorem ipsum is simply dummy</div>
  <div class="info-item" style="top:170px"><svg width="18" height="18" viewBox="0 0 24 24"><path d="M6 2l4 5-2 3c1 3 3 5 6 6l3-2 5 4-2 4C10 22 2 14 2 4z" fill="#fff"/></svg>1-888-555-0142</div>
  <div class="info-item" style="top:234px"><svg width="20" height="16" viewBox="0 0 20 16"><rect x="1" y="1" width="18" height="14" fill="#fff"/><path d="M1 1l9 7 9-7" fill="none" stroke="#0f2233" stroke-width="1.5"/></svg>hello@quorvane.com</div>
  <div class="social" aria-label="Social media links"><span></span><span></span><span></span></div>
</section>

<footer class="site-footer">© <b>QUORVANE SERVICE 2016</b> - All Rights Reserved</footer>

</body>
</html>
```